Business Card Design for Marketing Firm

Looking for business card design for higher end marketing firm. Clean but impressionable/trendy. We are a marketing firm that represents manufacturers in the foodservice equipment and supply industry. Our customers are end users such has hotels, restaurants, country clubs, convention centers and casinos as well as distributors of restaurants supplies and equipment, and manufacturers of foodservice equipment and supplies.
Target Market(s)
Hotels, Restaurants, Supply & Equipment Distributors, Foodservice Manufacturers
Industry/Entity Type
Foodservice/Hospitality
Contact Information for Business Card
Name, Title, Contact Number, Email, Website, Social Media, Address
Requirements
Must have
- Clean & Simple but Serious and Impressionable

```html
<!DOCTYPE html>
<html lang="en">
<head>
<meta charset="utf-8">
<title>Harbor Table Partners – Business Card</title>
<link href="https://fonts.googleapis.com/css2?family=Cinzel:wght@700&family=Arimo:wght@400&display=swap" rel="stylesheet">
<style>
  :root {
    --navy: #1c1f5c;
    --paper: #fbfbfb;
    --backdrop: #d8dbdc;
    --ink-soft: #4a4a4f;
    --emboss: #f0f1f2;
  }
  * { margin: 0; padding: 0; box-sizing: border-box; }
  html, body { width: 1200px; height: 829px; overflow: hidden; }
  body {
    background: var(--backdrop);
    display: flex;
    align-items: center;
    justify-content: center;
    gap: 60px;
  }
  .card {
    position: relative;
    width: 520px;
    height: 300px;
    background: var(--paper);
    box-shadow: 0 10px 28px rgba(0,0,0,0.12);
    overflow: hidden;
  }
  .wordmark {
    font-family: "Cinzel", serif;
    font-weight: 700;
    color: var(--navy);
    letter-spacing: 0.04em;
    white-space: nowrap;
  }

  /* Front: contact side */
  .card-front .wordmark {
    position: absolute;
    left: 40px;
    top: 40px;
    font-size: 17px;
  }
  .accent-square {
    position: absolute;
    left: 0;
    top: 86px;
    width: 12px;
    height: 26px;
    background: var(--navy);
  }
  .person {
    position: absolute;
    left: 40px;
    top: 84px;
  }
  .person-name {
    font-family: "Cinzel", serif;
    font-weight: 700;
    font-size: 21px;
    color: var(--navy);
    letter-spacing: 0.02em;
  }
  .person-title {
    font-family: "Arimo", sans-serif;
    font-size: 12px;
    color: var(--ink-soft);
    margin-top: 1px;
  }
  .contact-list {
    position: absolute;
    left: 40px;
    top: 142px;
    list-style: none;
    font-family: "Arimo", sans-serif;
    font-size: 12.5px;
    color: var(--ink-soft);
  }
  .contact-list li {
    display: flex;
    align-items: center;
    gap: 7px;
    height: 19px;
  }
  .contact-list svg { width: 11px; height: 11px; flex: none; fill: var(--ink-soft); }
  .social-dot {
    width: 9px; height: 9px; border-radius: 50%;
    background: var(--ink-soft); flex: none; margin: 0 1px;
  }
  .emboss-mark {
    position: absolute;
    right: 40px;
    top: 90px;
    width: 150px;
    height: 150px;
    border-radius: 50%;
    background: var(--emboss);
    box-shadow: inset 2px 2px 4px rgba(255,255,255,0.9), inset -2px -2px 4px rgba(0,0,0,0.06);
  }
  .address {
    position: absolute;
    right: 28px;
    bottom: 22px;
    font-family: "Arimo", sans-serif;
    font-size: 12.5px;
    line-height: 1.3;
    color: var(--ink-soft);
  }
  .accent-bar {
    position: absolute;
    left: 300px;
    bottom: 0;
    width: 150px;
    height: 8px;
    background: var(--navy);
  }

  /* Back: brand side */
  .card-back {
    display: flex;
    align-items: center;
    justify-content: center;
  }
  .card-back .wordmark { font-size: 30px; }
</style>
</head>
<body>
  <section class="card card-front" aria-label="Business card front">
    <div class="wordmark">Harbor Table Partners</div>
    <div class="accent-square"></div>
    <div class="person">
      <div class="person-name">Daniel Mercer</div>
      <div class="person-title">CEO/Founder</div>
    </div>
    <ul class="contact-list">
      <li>
        <svg viewBox="0 0 12 12" aria-hidden="true"><path d="M2.5 1h2l1 2.6-1.3 1a6 6 0 0 0 3.2 3.2l1-1.3L11 7.5v2a1.5 1.5 0 0 1-1.6 1.5A9.5 9.5 0 0 1 1 2.6 1.5 1.5 0 0 1 2.5 1z"/></svg>
        555-014-2273
      </li>
      <li>
        <svg viewBox="0 0 12 12" aria-hidden="true"><path d="M1 2.5h10v7H1z M1.6 3.1 6 6.4l4.4-3.3" fill="none" stroke="#4a4a4f" stroke-width="1"/></svg>
        info@harbortablepartners.com
      </li>
      <li>
        <svg viewBox="0 0 12 12" aria-hidden="true"><circle cx="6" cy="6" r="5" fill="none" stroke="#4a4a4f"/><path d="M1 6h10M6 1c-2.5 3-2.5 7 0 10M6 1c2.5 3 2.5 7 0 10" fill="none" stroke="#4a4a4f" stroke-width="0.8"/></svg>
        www.harbortablepartners.com
      </li>
      <li>
        <span class="social-dot"></span>
        @harbortablepartners
      </li>
    </ul>
    <div class="emboss-mark" role="img" aria-label="Blind-embossed brand emblem"></div>
    <address class="address" style="font-style:normal">48 Quay Road, Suite 210<br>Lakeview, ON 20417</address>
    <div class="accent-bar"></div>
  </section>

  <section class="card card-back" aria-label="Business card back">
    <div class="wordmark">Harbor Table Partners</div>
  </section>
</body>
</html>
```